Business card design

We need a business card designed completed for a new company. We are a company that works with associations, schools to convert their older text/DVDs into dynamic online and mobile programs. Our initial platform is designed for the legal associations and will enable their lawyers to access their content such as forms, videos, case law and support materials anywhere, anytime. We are also focused on Project Management Associations, Financial Management Associations and IT Associations.

I would like for the business card to have the following information:

Logo

Kent marrowby

President and CEO

kmarrowby@trevantiq.example

Mobile: 555-374-9160

www.trevantiq.example

Tag line: Transforming content into a mobile platform    

I would like it to be double sided, use the colours of the logo, tie into the mobile world

 

Industry/Entity Type

Legal

Logo Text

Trevantiq

```html
<!DOCTYPE html>
<html lang="en">
<head>
<meta charset="utf-8">
<title>Trevantiq business card</title>
<link rel="stylesheet" href="https://fonts.googleapis.com/css2?family=Open+Sans:ital,wght@0,400;0,600;0,700;1,700&display=swap">
<style>
  :root {
    --backdrop: #e9e7e4;
    --label: #222222;
    --card-grey: #9b9b9b;
    --card-white: #ffffff;
    --band-dark: #6b6b6b;
    --swoosh-light: #ffffff;
    --swoosh-grey: #a3a3a3;
    --ink-light: #ffffff;
    --ink-dark: #555555;
    --brand-on-white: #6e6e6e;
    --rule-dark: #5a5a5a;
  }
  * { box-sizing: border-box; margin: 0; padding: 0; }
  html, body { width: 1200px; height: 800px; overflow: hidden; }
  body {
    position: relative;
    background: var(--backdrop);
    font-family: "Open Sans", Arial, sans-serif;
  }
  .side-label {
    position: absolute;
    width: 508px;
    text-align: center;
    font-size: 20px;
    color: var(--label);
  }
  .card {
    position: absolute;
    width: 508px;
    height: 289px;
    border-radius: 22px;
    overflow: hidden;
    box-shadow: 0 3px 10px rgba(0,0,0,.25);
  }
  .card--grey { background: var(--card-grey); color: var(--ink-light); }
  .card--white { background: var(--card-white); color: var(--ink-dark); }
  .card__waves { position: absolute; inset: 0; width: 100%; height: 100%; }
  .brand {
    position: absolute;
    font-weight: 700;
    letter-spacing: -1px;
    line-height: 1;
    white-space: nowrap;
  }
  .card--grey .brand { color: var(--ink-light); }
  .card--white .brand { color: var(--brand-on-white); }
  .brand--front { left: 22px; top: 46px; font-size: 52px; }
  .brand--centered { left: 0; right: 0; top: 108px; text-align: center; font-size: 74px; }
  .contact {
    position: absolute;
    left: 304px;
    top: 58px;
    padding-left: 13px;
    border-left: 1px solid var(--rule-dark);
    font-size: 11.5px;
    line-height: 1.3;
    white-space: nowrap;
  }
  .card--white .contact { border-left-color: #888; }
  .contact__name { font-size: 14.5px; font-weight: 700; }
  .contact__title { margin-bottom: 6px; }
  .contact__line { margin-top: 8px; }
  .contact__key { font-weight: 700; font-style: italic; }
  .tagline {
    position: absolute;
    left: 32px;
    top: 238px;
    font-size: 14.5px;
    line-height: 1.3;
    color: var(--ink-light);
  }
  .tagline span { display: block; padding-left: 4px; }
  .tagline span:first-child { padding-left: 0; }
  .web {
    position: absolute;
    left: 0; right: 0;
    top: 252px;
    text-align: center;
    font-size: 16px;
    letter-spacing: 3px;
  }
  .card--grey .web { color: #2c2c2c; }
  .card--white .web { color: #333; }
</style>
</head>
<body>
  <div class="side-label" style="left:80px;top:50px;">Front</div>
  <div class="side-label" style="left:637px;top:50px;">Back - 1</div>
  <div class="side-label" style="left:73px;top:409px;">Back - 2</div>
  <div class="side-label" style="left:634px;top:409px;">Back - 3</div>

  <section class="card card--grey" style="left:80px;top:98px;">
    <svg class="card__waves" viewBox="0 0 508 289" preserveAspectRatio="none" aria-hidden="true">
      <path d="M0,232 C110,214 210,226 300,250 C380,266 440,240 508,214 L508,289 L0,289 Z" fill="var(--band-dark)"/>
      <path d="M110,208 C240,206 330,260 508,208 L508,220 C360,266 250,220 110,208 Z" fill="var(--swoosh-light)"/>
    </svg>
    <div class="brand brand--front">Trevantiq</div>
    <div class="contact">
      <div class="contact__name">Kent marrowby</div>
      <div class="contact__title">President and CEO</div>
      <div class="contact__line"><span class="contact__key">C</span> : 555-374-9160</div>
      <div class="contact__line"><span class="contact__key">E</span> : kmarrowby@trevantiq.example</div>
      <div class="contact__line"><span class="contact__key">W</span> : www.trevantiq.example</div>
    </div>
    <p class="tagline"><span>Transforming content</span><span>into a mobile platform</span></p>
  </section>

  <section class="card card--white" style="left:637px;top:98px;">
    <svg class="card__waves" viewBox="0 0 508 289" preserveAspectRatio="none" aria-hidden="true">
      <path d="M0,232 C110,214 210,226 300,250 C380,266 440,240 508,214 L508,289 L0,289 Z" fill="var(--band-dark)"/>
      <path d="M110,208 C240,206 330,260 508,208 L508,220 C360,266 250,220 110,208 Z" fill="var(--swoosh-grey)"/>
    </svg>
    <div class="brand brand--front">Trevantiq</div>
    <div class="contact">
      <div class="contact__name">Kent marrowby</div>
      <div class="contact__title">President and CEO</div>
      <div class="contact__line"><span class="contact__key">C</span> : 555-374-9160</div>
      <div class="contact__line"><span class="contact__key">E</span> : kmarrowby@trevantiq.example</div>
      <div class="contact__line"><span class="contact__key">W</span> : www.trevantiq.example</div>
    </div>
    <p class="tagline"><span>Transforming content</span><span>into a mobile platform</span></p>
  </section>

  <section class="card card--grey" style="left:73px;top:452px;">
    <div class="brand brand--centered">Trevantiq</div>
    <div class="web">www.trevantiq.example</div>
  </section>

  <section class="card card--white" style="left:634px;top:450px;">
    <div class="brand brand--centered">Trevantiq</div>
    <div class="web">www.trevantiq.example</div>
  </section>
</body>
</html>
```